Business Card Design needed for start up company Halvora

In need of a new business card designed for a start up company based in Sydney, Halvora is a new start up innovative Company, our mission it to make property accessible for everyday Australian and to become the leading Real Estate platform in Australia. We want it to be fresh and clean.

Industry/Entity Type

Financial

Contact Information for Business Card

Section for Name
Section for Title

HALVORA - The Strength of Pooling
Mobile:
Direct:

Font styles to use
Sans Serif

Colors
33a6d7
0692cd
0255a3
ffffff

Requirements
Must have
• Logo, all business card details

```html
<!DOCTYPE html>
<html lang="en">
<head>
<meta charset="utf-8">
<title>Halvora Business Card</title>
<link rel="stylesheet" href="https://fonts.googleapis.com/css2?family=Open+Sans:wght@400;600;700;800&display=swap">
<style>
  :root{
    --stage:#2a2a2c;
    --navy:#23409a;
    --navy-light:#3455ac;
    --sky:#4fc0ec;
    --white:#ffffff;
    --ink:#3a3a3a;
    --rule:#b5b5b5;
  }
  *{box-sizing:border-box;margin:0;padding:0}
  html,body{width:1200px;height:1000px;overflow:hidden;background:var(--stage);font-family:"Open Sans",sans-serif}
  .stage{width:1200px;height:1000px;display:flex;flex-direction:column;align-items:center;justify-content:center;gap:56px}
  .card{width:660px;height:377px;position:relative;box-shadow:0 18px 40px rgba(0,0,0,.45)}
  .card-front{background:linear-gradient(120deg,var(--navy) 0%,var(--navy-light) 100%);color:var(--white)}
  .card-back{background:var(--white)}
  .brand-name{position:absolute;left:50%;transform:translate(-50%,-50%);font-weight:800;letter-spacing:-1px;line-height:1;white-space:nowrap}
  .card-front .brand-name{top:46%;font-size:72px;color:var(--white)}
  .card-back .brand-name{top:72px;font-size:58px;color:var(--navy)}
  .tagline{position:absolute;left:0;right:0;bottom:28px;text-align:center;font-size:12px;letter-spacing:5px;font-weight:400}
  .details{position:absolute;top:168px;left:0;right:0;display:flex;justify-content:center;align-items:stretch;gap:26px}
  .identity{text-align:right;padding-top:8px}
  .person-name{font-size:27px;font-weight:700;color:var(--navy);letter-spacing:.5px;line-height:1.1}
  .person-title{font-size:21px;font-weight:600;color:var(--sky);line-height:1.2}
  .divider{width:3px;background:var(--rule)}
  .contacts{list-style:none;font-size:17px;color:var(--ink);line-height:1.5}
  .contacts li{display:flex;align-items:center;gap:12px}
  .contacts svg{width:14px;height:14px;fill:var(--sky);flex:none}
  .contacts .accent{color:var(--sky)}
  .address{position:absolute;left:0;right:0;bottom:34px;display:flex;justify-content:center;align-items:center;gap:10px;font-size:17px;color:var(--ink)}
  .address svg{width:20px;height:20px;fill:none;stroke:var(--sky);stroke-width:1.6;stroke-linejoin:round}
</style>
</head>
<body>
<main class="stage">
  <section class="card card-front" aria-label="Card front">
    <p class="brand-name">HALVORA</p>
    <p class="tagline">THE STRENGTH OF POOLING</p>
  </section>

  <section class="card card-back" aria-label="Card back">
    <p class="brand-name">HALVORA</p>
    <div class="details">
      <div class="identity">
        <p class="person-name">DANIEL REYES</p>
        <p class="person-title">Director</p>
      </div>
      <div class="divider"></div>
      <ul class="contacts">
        <li><svg viewBox="0 0 24 24"><path d="M6.6 10.8a15 15 0 0 0 6.6 6.6l2.2-2.2a1 1 0 0 1 1-.25 11.4 11.4 0 0 0 3.6.57 1 1 0 0 1 1 1V20a1 1 0 0 1-1 1A17 17 0 0 1 3 4a1 1 0 0 1 1-1h3.5a1 1 0 0 1 1 1 11.4 11.4 0 0 0 .57 3.6 1 1 0 0 1-.25 1z"/></svg><span>000 123 456 789</span></li>
        <li><svg viewBox="0 0 24 24"><path d="M7 1h10a2 2 0 0 1 2 2v18a2 2 0 0 1-2 2H7a2 2 0 0 1-2-2V3a2 2 0 0 1 2-2zm0 3v14h10V4zm5 15.5a1 1 0 1 0 0 2 1 1 0 0 0 0-2z"/></svg><span>000 222 3334</span></li>
        <li><svg viewBox="0 0 24 24"><path d="M2 5h20v14H2zm2 2v.5l8 5 8-5V7zm0 2.8V17h16V9.8l-8 5z"/></svg><span>urname@email.com</span></li>
        <li><svg viewBox="0 0 24 24"><path d="M12 2a10 10 0 1 0 0 20 10 10 0 0 0 0-20zm6.9 9h-3a15 15 0 0 0-1.3-5.6A8 8 0 0 1 18.9 11zM12 4.1c.9 1.2 1.8 3.6 1.9 6.9h-3.8c.1-3.3 1-5.7 1.9-6.9zM9.4 5.4A15 15 0 0 0 8.1 11h-3a8 8 0 0 1 4.3-5.6zM5.1 13h3a15 15 0 0 0 1.3 5.6A8 8 0 0 1 5.1 13zm6.9 6.9c-.9-1.2-1.8-3.6-1.9-6.9h3.8c-.1 3.3-1 5.7-1.9 6.9zm2.6-1.3a15 15 0 0 0 1.3-5.6h3a8 8 0 0 1-4.3 5.6z"/></svg><span>www.<span class="accent">websitename</span>.com</span></li>
      </ul>
    </div>
    <p class="address"><svg viewBox="0 0 24 24"><path d="M21 3 3 10.5l7.5 3L13.5 21z M21 3 10.5 13.5"/></svg><span>Your Street Address, Sydney, 1234</span></p>
  </section>
</main>
</body>
</html>
```